Kinesiology undergraduate program needs an infographic

We would like an infographic to creatively and succinctly inform students, faculty, staff, and others about our undergraduate values and competencies (perhaps also integrating our mission and vision). We would like to see a design that incorporates the definition of Kinesiology (the study of human movement) and the colors of our Westbrook State University at Harlan.

```html
<!DOCTYPE html>
<html lang="en">
<head>
<meta charset="utf-8">
<title>WSUH Kinesiology — Undergraduate Values and Competencies</title>
<link rel="stylesheet" href="https://fonts.googleapis.com/css2?family=Anton&family=Montserrat:wght@800&family=Poppins:wght@300;400&display=swap">
<style>
  :root {
    --red: #e2121c;
    --navy: #1e2152;
    --blue: #1aa7d4;
    --ink: #222226;
    --rule: #bdbdbd;
    --margin-rule: #f08a8f;
    --paper: #ffffff;
  }
  * { margin: 0; padding: 0; box-sizing: border-box; }
  html, body { width: 1200px; height: 849px; overflow: hidden; background: var(--paper); }
  .infographic {
    position: relative;
    width: 1200px;
    height: 849px;
    overflow: hidden;
    background:
      repeating-linear-gradient(to bottom, transparent 0 50px, var(--rule) 50px 51.5px) 0 -2px / 100% 100%,
      var(--paper);
    font-family: "Poppins", Arial, sans-serif;
    font-weight: 300;
    color: var(--ink);
  }
  .margin-rule { position: absolute; top: 0; bottom: 0; width: 1.5px; background: var(--margin-rule); }
  .margin-rule.first { left: 148px; }
  .margin-rule.second { left: 157px; }

  .section-title {
    position: absolute;
    font-family: "Anton", Impact, sans-serif;
    font-size: 46px;
    line-height: 1;
    color: var(--red);
    letter-spacing: 0.5px;
    background: var(--paper);
    padding: 0 4px;
  }
  .statement {
    position: absolute;
    font-size: 16.5px;
    line-height: 20.5px;
    text-align: center;
  }
  .mission-title { left: 496px; top: 56px; }
  .mission-text { left: 400px; width: 400px; top: 103px; }
  .values-title { left: 130px; top: 195px; }
  .values-text { left: 100px; width: 255px; top: 237px; }
  .vision-title { left: 882px; top: 195px; }
  .vision-text { left: 850px; width: 265px; top: 237px; }

  .figure-area {
    position: absolute;
    left: 362px; top: 232px;
    width: 500px; height: 570px;
    background: radial-gradient(ellipse at 40% 45%, rgba(184,74,52,0.85) 0%, rgba(210,140,120,0.55) 38%, rgba(220,220,222,0.5) 62%, rgba(255,255,255,0) 80%);
  }

  .competency { position: absolute; }
  .competency h2 {
    font-family: "Montserrat", Arial, sans-serif;
    font-weight: 800;
    font-size: 15.5px;
    line-height: 18px;
    color: var(--navy);
    text-transform: uppercase;
    letter-spacing: 0.2px;
  }
  .competency ul { list-style: none; font-size: 16.5px; line-height: 20.5px; }
  .intrapersonal { left: 123px; top: 493px; }
  .science { left: 123px; top: 654px; }
  .science h2 { margin-bottom: 0; }
  .reasoning { left: 860px; top: 493px; }
  .relationships { left: 860px; top: 654px; }

  .artwork { position: absolute; left: 0; top: 0; width: 1200px; height: 849px; pointer-events: none; }
</style>
</head>
<body>
<main class="infographic">
  <span class="margin-rule first"></span>
  <span class="margin-rule second"></span>

  <h1 class="section-title mission-title">OUR MISSION</h1>
  <p class="statement mission-text">To empower undergraduate students to pursue excellence through scientific discovery, clinical practice, and health promotion</p>

  <h1 class="section-title values-title">OUR VALUES</h1>
  <p class="statement values-text">Student Success, Science, and Service<br>Our Graduates Will Be Competent In...</p>

  <h1 class="section-title vision-title">OUR VISION</h1>
  <p class="statement vision-text">WSUH Kinesiology graduates are leaders who excel in careers that enhance the quality of life of individuals and communities</p>

  <div class="figure-area" role="img" aria-label="Illustration of a running human figure showing muscle anatomy beside a smooth white body, suggesting human movement"></div>

  <svg class="artwork" viewBox="0 0 1200 849" aria-hidden="true">
    <!-- values arrow -->
    <polygon points="219,340 233,340 226,354" fill="var(--navy)"/>

    <!-- connectors -->
    <g stroke="var(--ink)" stroke-width="1.3" fill="none">
      <polyline points="356,398 97,398 97,498 120,498"/>
      <polyline points="310,664 390,664 390,612 404,612"/>
      <polyline points="786,387 804,387 804,496 855,496"/>
      <polyline points="746,572 798,572 798,664 855,664"/>
    </g>
    <g fill="var(--ink)">
      <circle cx="356" cy="398" r="5"/>
      <circle cx="97" cy="498" r="4"/>
      <circle cx="310" cy="664" r="5"/>
      <circle cx="404" cy="612" r="4"/>
      <circle cx="786" cy="387" r="5"/>
      <circle cx="804" cy="496" r="4"/>
      <circle cx="746" cy="572" r="5"/>
      <circle cx="798" cy="664" r="4"/>
    </g>

    <!-- pencil icon -->
    <g transform="translate(112,420) rotate(45)" fill="none" stroke="var(--navy)" stroke-width="4" stroke-linejoin="round">
      <rect x="-7" y="-22" width="14" height="36"/>
      <polyline points="-7,14 0,26 7,14"/>
      <line x1="-7" y1="-14" x2="7" y2="-14"/>
    </g>

    <!-- heartbeat line -->
    <polyline fill="none" stroke="var(--navy)" stroke-width="2"
      points="175,446 205,446 212,438 216,458 222,400 228,466 234,440 240,446 280,446 286,438 290,458 296,400 302,466 308,440 314,446 350,446 356,438 360,458 366,400 372,466 378,440 384,446 425,446"/>

    <!-- weekly line chart -->
    <g font-family="Poppins, Arial, sans-serif" font-size="7.5" font-weight="700" fill="var(--ink)">
      <line x1="862" y1="394" x2="862" y2="454" stroke="var(--ink)" stroke-width="1.2"/>
      <line x1="862" y1="454" x2="1068" y2="454" stroke="var(--ink)" stroke-width="1.2"/>
      <text x="856" y="406" text-anchor="end">20:00</text>
      <text x="856" y="420" text-anchor="end">16:00</text>
      <text x="856" y="434" text-anchor="end">12:00</text>
      <text x="856" y="448" text-anchor="end">8:00</text>
      <text x="866" y="467">Mon</text>
      <text x="893" y="467">Tue</text>
      <text x="922" y="467">Wed</text>
      <text x="956" y="467">Thu</text>
      <text x="982" y="467">Fri</text>
      <text x="1016" y="467">Sat</text>
      <text x="1048" y="467">Sun</text>
      <path d="M862,434 C875,432 885,415 897,426 C907,437 912,427 922,420 C932,414 937,426 945,420 C955,410 955,398 965,400 C975,403 980,410 990,414 C1000,418 1002,432 1010,428 C1020,420 1022,402 1035,406 C1045,410 1045,432 1068,436" fill="none" stroke="var(--red)" stroke-width="1.8"/>
    </g>

    <!-- lightbulb icon -->
    <g fill="none" stroke="var(--navy)" stroke-width="4" stroke-linecap="round">
      <path d="M1114,494 C1100,484 1098,462 1112,452 C1124,443 1140,447 1146,458 C1152,470 1148,484 1138,494 Z"/>
      <line x1="1116" y1="502" x2="1136" y2="502"/>
      <line x1="1118" y1="510" x2="1134" y2="510"/>
      <line x1="1126" y1="432" x2="1126" y2="440"/>
      <line x1="1100" y1="444" x2="1105" y2="449"/>
      <line x1="1152" y1="444" x2="1147" y2="449"/>
      <line x1="1092" y1="468" x2="1099" y2="468"/>
      <line x1="1153" y1="468" x2="1160" y2="468"/>
    </g>

    <!-- atom icon -->
    <g fill="none" stroke="var(--navy)" stroke-width="4">
      <ellipse cx="78" cy="657" rx="34" ry="12"/>
      <ellipse cx="78" cy="657" rx="34" ry="12" transform="rotate(60 78 657)"/>
      <ellipse cx="78" cy="657" rx="34" ry="12" transform="rotate(-60 78 657)"/>
      <circle cx="78" cy="657" r="5" fill="var(--navy)"/>
    </g>

    <!-- network target icon -->
    <g fill="none" stroke="var(--navy)" stroke-width="4">
      <circle cx="1097" cy="659" r="35"/>
      <circle cx="1097" cy="659" r="25" stroke-width="2.5"/>
      <circle cx="1097" cy="659" r="13" stroke-width="3"/>
      <circle cx="1097" cy="659" r="4" fill="var(--navy)"/>
    </g>

    <!-- donut charts -->
    <g fill="none" stroke-width="11">
      <circle cx="430" cy="659" r="15" stroke="var(--red)"/>
      <path d="M430,644 A15,15 0 0 1 445,659" stroke="var(--navy)"/>
      <circle cx="430" cy="659" r="8" fill="var(--blue)" stroke="none"/>

      <circle cx="430" cy="719" r="15" stroke="var(--red)"/>
      <path d="M430,704 A15,15 0 0 1 442,710" stroke="var(--navy)"/>
      <circle cx="430" cy="719" r="8" fill="var(--blue)" stroke="none"/>

      <circle cx="430" cy="775" r="15" stroke="var(--navy)"/>
      <path d="M445,775 A15,15 0 0 1 430,790" stroke="var(--red)"/>
      <circle cx="430" cy="775" r="8" fill="var(--blue)" stroke="none"/>
    </g>

    <!-- progress band -->
    <rect x="830" y="815" width="122" height="6" fill="var(--red)"/>
    <rect x="952" y="815" width="123" height="6" fill="var(--blue)"/>
    <rect x="1075" y="815" width="125" height="6" fill="var(--red)"/>
    <circle cx="830" cy="818" r="7" fill="var(--blue)" stroke="var(--navy)" stroke-width="2"/>
    <circle cx="952" cy="818" r="7" fill="var(--blue)" stroke="var(--paper)" stroke-width="2"/>
    <circle cx="1075" cy="818" r="7" fill="var(--navy)" stroke="var(--blue)" stroke-width="2"/>
  </svg>

  <section class="competency intrapersonal">
    <h2>Intrapersonal Growth</h2>
    <ul>
      <li>Cultural Humility/Sensitivity</li>
      <li>Integrity</li>
      <li>Self-Directed</li>
      <li>Dependability</li>
      <li>Mission Oriented</li>
    </ul>
  </section>

  <section class="competency science">
    <h2>The Science of<br>Kinesiology</h2>
    <ul>
      <li>Foundational Concepts of<br>Kinesiology</li>
      <li>Clinical Application</li>
      <li>Scientific Communication</li>
    </ul>
  </section>

  <section class="competency reasoning">
    <h2>Thinking and Reasoning</h2>
    <ul>
      <li>Critical Thinking</li>
      <li>Quantitative Reasoning</li>
      <li>Scientific Inquiry</li>
      <li>Concept Integration</li>
    </ul>
  </section>

  <section class="competency relationships">
    <h2>Relationships and<br>Communication</h2>
    <ul>
      <li>Cultural Competence</li>
      <li>Professionalism</li>
      <li>Leadership and Teamwork</li>
      <li>Service</li>
      <li>Orientation/Citizenship</li>
    </ul>
  </section>
</main>
</body>
</html>
```